HearthMile business card and stationary design

We are looking for a simple yet elegant design for our mortgage company business card and stationary.

The card should include:
Name (Marcus Pell)
Title (CEO)
Phone Number (732-555-0182)
Address (48 Birchwell Court, Suite 314, Larkmoor, NJ 07790)
Email (email@hearthmile.example)
"NMLS" i.e. (NMLS 61947)
"Company NMLS" (Company NMLS 274615)

Contact Information for Business Card

See above

```html
<!DOCTYPE html>
<html lang="en">
<head>
<meta charset="utf-8">
<title>HearthMile Business Card</title>
<link rel="stylesheet" href="https://fonts.googleapis.com/css2?family=Montserrat:wght@500;600&family=Arimo:wght@400&display=swap">
<style>
  :root {
    --stage: #2b2b2d;
    --card: #1c1d1f;
    --accent: #0aa9e6;
    --ink-light: #ffffff;
    --rule: #7d7f84;
    --icon-ink: #0d2a38;
  }
  * { box-sizing: border-box; margin: 0; padding: 0; }
  html, body {
    width: 1200px; height: 1108px; overflow: hidden;
    background: var(--stage);
  }
  .stage {
    position: relative; width: 1200px; height: 1108px;
    display: flex; justify-content: center; align-items: center; gap: 60px;
  }
  .card {
    position: relative; width: 420px; height: 735px;
    background: var(--card); border-radius: 22px;
    box-shadow: 0 18px 40px rgba(0,0,0,.45);
    overflow: hidden;
  }
  .card--front {
    display: flex; flex-direction: column; align-items: center;
    font-family: "Arimo", Arial, sans-serif; color: var(--ink-light);
    text-align: center; padding-top: 150px;
  }
  .wordmark {
    font-family: "Montserrat", Arial, sans-serif; font-weight: 500;
    font-size: 58px; letter-spacing: 0.5px; color: var(--ink-light);
    line-height: 1; white-space: nowrap;
  }
  .person { margin-top: 86px; }
  .person__name {
    font-family: "Montserrat", Arial, sans-serif; font-weight: 600;
    font-size: 31px; color: var(--accent); line-height: 1.1;
  }
  .person__title { font-size: 22px; margin-top: 2px; }
  .icon-rule {
    display: flex; align-items: center; gap: 10px; margin-top: 12px; width: 290px;
  }
  .icon-rule::before, .icon-rule::after {
    content: ""; flex: 1; height: 1px; background: var(--rule);
  }
  .icon-row { display: flex; gap: 6px; }
  .icon { width: 36px; height: 36px; display: block; }
  .contact { margin-top: 10px; font-size: 21px; line-height: 1.3; }
  .rule { width: 290px; height: 1px; background: var(--rule); margin: 18px 0; }
  .address { font-size: 21px; line-height: 1.3; }
  .licence { font-size: 21px; line-height: 1.35; }
  .licence__label { color: var(--accent); }

  .back-texture {
    position: absolute; inset: 0;
    background: linear-gradient(135deg, #26272a 0%, #1a1b1d 45%, #222326 70%, #17181a 100%);
  }
  .back-wordmark {
    position: absolute; right: 44px; bottom: 150px;
    font-family: "Montserrat", Arial, sans-serif; font-weight: 500;
    font-size: 44px; color: var(--ink-light); line-height: 1;
  }
</style>
</head>
<body>
<main class="stage">
  <section class="card card--front" aria-label="Business card front">
    <div class="wordmark">HearthMile</div>

    <div class="person">
      <div class="person__name">Marcus Pell</div>
      <div class="person__title">CEO</div>
    </div>

    <div class="icon-rule">
      <div class="icon-row">
        <svg class="icon" viewBox="0 0 36 36" aria-label="Phone">
          <rect width="36" height="36" rx="4" fill="var(--accent)"/>
          <path d="M9 14c0-3 4-5 9-5s9 2 9 5l-3 1-1-2c-3-1-7-1-10 0l-1 2z" fill="var(--icon-ink)"/>
          <rect x="11" y="17" width="14" height="10" rx="2" fill="var(--icon-ink)"/>
          <circle cx="18" cy="22" r="2.5" fill="var(--accent)"/>
        </svg>
        <svg class="icon" viewBox="0 0 36 36" aria-label="Email">
          <rect width="36" height="36" rx="4" fill="var(--accent)"/>
          <rect x="7" y="11" width="22" height="15" fill="none" stroke="var(--icon-ink)" stroke-width="2"/>
          <path d="M7 11l11 9 11-9M7 26l8-7M29 26l-8-7" fill="none" stroke="var(--icon-ink)" stroke-width="1.6"/>
        </svg>
        <svg class="icon" viewBox="0 0 36 36" aria-label="Website">
          <rect width="36" height="36" rx="4" fill="var(--accent)"/>
          <circle cx="18" cy="18" r="10" fill="none" stroke="var(--icon-ink)" stroke-width="2"/>
          <path d="M8 18h20M18 8c-5 6-5 14 0 20M18 8c5 6 5 14 0 20" fill="none" stroke="var(--icon-ink)" stroke-width="1.5"/>
        </svg>
      </div>
    </div>

    <div class="contact">
      <div>732-555-0182</div>
      <div>email@hearthmile.example</div>
      <div>www.hearthmile.example</div>
    </div>

    <div class="rule"></div>

    <div class="address">
      <div>48 Birchwell Court, Suite 314</div>
      <div>Larkmoor, NJ 07790</div>
    </div>

    <div class="rule"></div>

    <div class="licence">
      <div><span class="licence__label">NMLS</span> 61947</div>
      <div><span class="licence__label">Company NMLS</span> 274615</div>
    </div>
  </section>

  <section class="card card--back" aria-label="Business card back">
    <div class="back-texture" role="img" aria-label="Tonal spot-gloss pattern of the repeated company name running diagonally across the card"></div>
    <div class="back-wordmark">HearthMile</div>
  </section>
</main>
</body>
</html>
```